Marlowe Crest Realty business card design

Looking for an upscale and clean business card design and updated logo. I sell to a very high-end south Florida real estate market.
Target Market(s)
High-end real estate in south Florida real estate market
Industry/Entity Type
Real Estate Agent
Contact Information for Business Card
Marlowe Crest Realty, Inc
738 West Pinecrest Ave, Suite 410/510, Fort Lauderdale, FL 33308
Gary Whitlock - Broker/Owner
954-327-8846 Direct
garyshomes@quellmail.com
Website: DwellTarrowBay.com
Font styles to use
Other font styles liked:
- Copperplate Gothic, Georgia, etc.
Requirements
Must have
- My photo, company name, my name and title, all info stated in Details above
Nice to have
- Luxury home design element, waterfront

```html
<!DOCTYPE html>
<html lang="en">
<head>
<meta charset="utf-8">
<title>Marlowe Crest Realty – Business Card</title>
<link rel="stylesheet" href="https://fonts.googleapis.com/css2?family=EB+Garamond:wght@400;700&display=swap">
<style>
  :root {
    --backdrop: #c9cacd;
    --card-black: #000000;
    --card-yellow: #efc900;
    --sun-yellow: #e8c40a;
    --ink-white: #ffffff;
    --ink-olive: #5e5200;
    --photo-light: #d9d9d9;
    --photo-dark: #4a4a4a;
  }
  * { box-sizing: border-box; margin: 0; padding: 0; }
  html, body {
    width: 1200px; height: 857px; overflow: hidden;
    background: var(--backdrop);
    font-family: "EB Garamond", Georgia, serif;
  }
  .canvas {
    width: 1200px; height: 857px;
    display: flex; align-items: center; justify-content: center; gap: 40px;
  }
  .card {
    width: 540px; height: 309px; position: relative; overflow: hidden;
    box-shadow: 0 6px 18px rgba(0,0,0,0.18);
  }

  /* Front */
  .card-front { background: var(--card-black); }
  .brand {
    position: absolute; left: 120px; top: 104px;
    display: flex; align-items: center; gap: 22px;
  }
  .brand-dot {
    width: 84px; height: 84px; border-radius: 50%;
    background: var(--sun-yellow); flex: none;
  }
  .brand-name {
    color: var(--ink-white); font-weight: 400; font-size: 30px; line-height: 1.15;
    letter-spacing: 0.5px;
  }
  .brand-name .line2 { display: block; padding-left: 36px; }

  /* Back */
  .card-back { background: var(--card-yellow); }
  .portrait {
    position: absolute; right: 0; bottom: 0; width: 200px; height: 270px;
    background: linear-gradient(160deg, var(--photo-light) 0%, #9a9a9a 45%, var(--photo-dark) 100%);
    border-top-left-radius: 100px 110px;
  }
  .details { position: absolute; left: 34px; top: 78px; color: var(--ink-olive); }
  .agent-name {
    color: var(--ink-white); font-weight: 700; font-size: 34px; line-height: 1;
    letter-spacing: 0.5px;
  }
  .agent-title { font-size: 17px; padding-left: 52px; margin-top: 2px; }
  .contact { margin-top: 22px; font-size: 16px; line-height: 1.2; }
  .contact .company { font-weight: 700; font-size: 18px; }
</style>
</head>
<body>
<main class="canvas">
  <section class="card card-front" aria-label="Card front">
    <div class="brand">
      <span class="brand-dot" aria-hidden="true"></span>
      <p class="brand-name">Marlowe Crest<span class="line2">Realty, Inc.</span></p>
    </div>
  </section>

  <section class="card card-back" aria-label="Card back">
    <div class="portrait" role="img" aria-label="Black and white portrait photo of the broker"></div>
    <div class="details">
      <h1 class="agent-name">Gary Whitlock</h1>
      <p class="agent-title">Broker/Owner</p>
      <div class="contact">
        <p class="company">Marlowe Crest Realty, Inc</p>
        <p>738 West Pinecrest Ave, Suite 410/510</p>
        <p>Fort Lauderdale, FL 33308</p>
        <p>954-327-8846 Direct</p>
        <p>garyshomes@quellmail.com</p>
        <p>Website: DwellTarrowBay.com</p>
      </div>
    </div>
  </section>
</main>
</body>
</html>
```